Visitenkarten-Design für das Business mit Gesundheit& Beauty
Zielgruppe
Ich bin selbständige Vertriebspartnerin von Vk. Die Visitenkarten sollen nicht zu verspielt wirken, eher geschäftlich. Dennoch könnte eine Verbindung zu den Bereichen Gesundheit & Beuuty dazukommen .
Hauptproduktmerkmal ist zum Beispiel die Aloe Vera, Naturprodukte.. mehr Infos auf : www.bettina-kolmar-beispiel.de
Instagram :bettikolmar
Eventuell könnte mein Slogan mit 'just more' noch einfließen, muss aber nicht. Bin für Ideen offen...
Aufgabenstellung
elegant und zeitlos, aber weich
Vielleicht eine goldene Aloe Vera irgendwie mit drauf?
Habe bei den dateien mal ein paar Screenshots hinzugefügt was ich recht schön fand

```html
<!DOCTYPE html>
<html lang="de">
<head>
<meta charset="utf-8">
<title>Bettina Kolmar – Visitenkarte</title>
<link rel="stylesheet" href="https://fonts.googleapis.com/css2?family=Josefin+Sans:wght@300;400&display=swap">
<style>
  :root {
    --backdrop: #dcdcdc;
    --card-dark: #474747;
    --card-light: #f1f2f0;
    --gold: #b89a72;
    --gold-deep: #9a7b55;
    --gold-soft: #eadfce;
    --ink: #1d1d1d;
  }
  * { box-sizing: border-box; margin: 0; padding: 0; }
  html, body {
    width: 1200px; height: 842px; overflow: hidden;
    background: var(--backdrop);
    font-family: "Josefin Sans", sans-serif;
  }
  .canvas { position: relative; width: 1200px; height: 842px; }

  .card {
    position: absolute;
    width: 480px; height: 290px;
    top: 120px;
    overflow: hidden;
  }
  .card--front { left: 90px; background: var(--card-dark); }
  .card--back { left: 630px; background: var(--card-light); }

  .wordmark {
    position: absolute;
    display: flex; align-items: center; gap: 14px;
    font-weight: 300; letter-spacing: 0.08em; text-transform: uppercase;
    white-space: nowrap;
  }
  .wordmark__ring { flex: none; }
  .wordmark--front { left: 0; right: 0; top: 118px; justify-content: center; font-size: 26px; color: var(--gold); }

  .leaf-pattern {
    position: absolute; inset: 0;
    background:
      radial-gradient(ellipse at 30% 55%, rgba(234,223,206,0.85), rgba(234,223,206,0) 60%),
      radial-gradient(ellipse at 75% 35%, rgba(234,223,206,0.6), rgba(234,223,206,0) 55%),
      linear-gradient(120deg, var(--gold-soft) 0%, var(--card-light) 70%);
  }
  .wordmark--back { left: 34px; top: 92px; font-size: 21px; color: var(--gold-deep); }

  .contact {
    position: absolute; left: 270px; top: 34px;
    font-size: 11.5px; font-weight: 300; color: var(--gold-deep);
    line-height: 1.6;
    display: grid; grid-template-columns: 44px auto;
  }
  .tagline {
    position: absolute; right: 34px; bottom: 40px;
    font-size: 15px; font-weight: 400; letter-spacing: 0.32em;
    color: var(--ink); text-transform: uppercase;
  }
  .tagline__amp { font-size: 10px; letter-spacing: 0.2em; }

  .lockup {
    position: absolute; left: 0; right: 0; top: 560px;
    justify-content: center; font-size: 34px; color: var(--ink);
  }
</style>
</head>
<body>
<main class="canvas">

  <section class="card card--front" aria-label="Vorderseite">
    <div class="wordmark wordmark--front">
      <svg class="wordmark__ring" width="26" height="26" viewBox="0 0 26 26" aria-hidden="true">
        <circle cx="13" cy="13" r="11.5" fill="none" stroke="var(--gold)" stroke-width="1.4"/>
      </svg>
      <span>Bettina Kolmar</span>
    </div>
  </section>

  <section class="card card--back" aria-label="Rückseite">
    <div class="leaf-pattern" role="img" aria-label="Streumuster aus zarten goldenen Blättern"></div>

    <div class="wordmark wordmark--back">
      <svg class="wordmark__ring" width="20" height="20" viewBox="0 0 20 20" aria-hidden="true">
        <circle cx="10" cy="10" r="8.8" fill="none" stroke="var(--gold-deep)" stroke-width="1.2"/>
      </svg>
      <span>Bettina Kolmar</span>
    </div>

    <dl class="contact">
      <dt>Tel.:</dt><dd>+49 170 5550142</dd>
      <dt>E-mail:</dt><dd>info@bettina-kolmar-beispiel.de</dd>
      <dt>Web:</dt><dd>www.bettina-kolmar-beispiel.de</dd>
    </dl>

    <p class="tagline">Health, Beauty <span class="tagline__amp">&amp;</span> More</p>
  </section>

  <div class="wordmark lockup">
    <svg class="wordmark__ring" width="34" height="34" viewBox="0 0 34 34" aria-hidden="true">
      <circle cx="17" cy="17" r="15.5" fill="none" stroke="var(--gold)" stroke-width="1.6"/>
    </svg>
    <span>Bettina Kolmar</span>
  </div>

</main>
</body>
</html>
```